Toronto's Airline, based in Downtown looking for a whole new look and feel.

SkyMerrow is looking for a new look in our website. We are an airline based at Corwin Hale Airfield in Toronto. You can view our current website/services at www.skymerrow-example.com. We are expanding our services and look forward to a very sleek and modernized website. Please view the different pages on our website, we also need to add several new plane types as we have expanded and the website is not current. Would also be interesting to have a news feed or update feed through a widget which would be easy to use and update. we will also be implementing 2 third party programs called tavlo and quenbrook on the website, both are tour based and airline based sales and management functions.

Target Market(s)

Commuters, travel, tourism, dates, general public

Industry/Entity Type

Airline

Coding

Coded - Design and coding required

Number of Pages Required

5+ page

Font styles to use
Other font styles liked:
• Toronto subway font would be nice

Requirements
Must have
• A modern feel, easy to use, our booking function is currently a bit confusing which we will be working on. Content can be taken from our current website www.skymerrow-example.com
Nice to have
• work with out theme colours of blue and light grey

```html
<!DOCTYPE html>
<html lang="en">
<head>
<meta charset="utf-8">
<title>SkyMerrow Airways</title>
<link href="https://fonts.googleapis.com/css2?family=Open+Sans:ital,wght@0,300;0,400;0,600;0,700;1,400;1,600&display=swap" rel="stylesheet">
<style>
:root{
  --blue:#3b6cb7;
  --blue-dark:#2f5a9c;
  --ink:#2e2e2e;
  --text:#555;
  --muted:#8a8a8a;
  --line:#dcdcdc;
  --light:#f4f5f7;
  --white:#fff;
}
*{box-sizing:border-box;margin:0;padding:0}
html,body{width:1200px;height:2936px;overflow:hidden;background:var(--white)}
body{position:relative;font-family:"Open Sans",Arial,sans-serif;color:var(--text)}
.abs{position:absolute}
a{color:inherit;text-decoration:none}

/* header */
.brand{left:98px;top:22px;display:flex;align-items:center;gap:12px}
.brand-dot{width:44px;height:44px;border-radius:50%;border:3px solid var(--blue)}
.brand-name{font-size:26px;font-weight:700;color:var(--blue);letter-spacing:.5px}
.phone-box{left:660px;top:20px;display:flex;gap:14px;align-items:flex-start}
.phone-icon{width:32px;height:32px;border-radius:50%;border:1px solid var(--line);display:flex;align-items:center;justify-content:center}
.phone-label{font-size:14px;color:var(--ink)}
.phone-number{font-size:24px;font-weight:700;color:var(--blue);line-height:1.2}
.btn{display:inline-flex;align-items:center;justify-content:center;background:var(--blue);color:var(--white);font-weight:700;border-radius:20px}
.btn-book-top{left:953px;top:25px;width:147px;height:38px;font-size:15px}
.nav{left:0;top:86px;width:1200px;height:43px;border-top:1px solid var(--line);border-bottom:1px solid var(--line)}
.nav-item{position:absolute;top:12px;font-size:14px;font-weight:600;color:var(--ink);letter-spacing:.2px;white-space:nowrap}
.nav-item.active{color:var(--blue)}
.search{left:812px;top:86px;width:288px;height:43px;border-left:1px solid var(--line);border-right:1px solid var(--line);padding:11px 16px;font-size:15px;color:#aaa}
.search svg{position:absolute;right:14px;top:14px}

/* hero */
.hero{left:0;top:129px;width:1200px;height:456px;background:linear-gradient(180deg,#6f8fb4 0%,#a9bbd0 35%,#c9b89a 52%,#47617e 60%,#2d4560 100%)}
.hero-title{left:0;top:222px;width:1200px;text-align:center;font-size:52px;font-weight:700;color:var(--white);letter-spacing:1px}
.booking{left:168px;top:309px;width:863px;height:161px;background:rgba(40,48,60,.72)}
.trip-types{left:424px;top:334px;display:flex;gap:42px;color:var(--white);font-size:15px}
.trip-types span{display:flex;align-items:center;gap:8px}
.radio{width:15px;height:15px;border-radius:50%;border:2px solid var(--white);display:inline-block}
.radio.on{background:radial-gradient(circle,var(--white) 35%,transparent 40%)}
.field{top:372px;height:45px;background:var(--white);border-right:1px solid var(--line);font-size:12px;color:#888;padding:15px 16px;display:flex;align-items:center;gap:6px;letter-spacing:.5px}
.btn-book-hero{left:847px;top:372px;width:151px;height:45px;font-size:16px;border-radius:0}
.dots{left:561px;top:514px;display:flex;gap:5px}
.dots i{width:15px;height:15px;border-radius:50%;border:2px solid var(--white);display:block}
.dots i.on{background:var(--white)}

/* welcome */
.welcome-pre{left:98px;top:638px;font-size:27px;font-weight:300;color:#666}
.welcome-title{left:98px;top:670px;font-size:27px;font-weight:700;color:var(--blue)}
.welcome-body{left:98px;top:720px;width:480px;font-size:12.5px;line-height:23px;color:var(--text)}
.welcome-body p{margin-bottom:18px}
.btn-more{left:98px;top:904px;width:120px;height:31px;border:1px solid #bbb;border-radius:16px;font-size:11px;font-weight:700;color:var(--blue);display:flex;align-items:center;justify-content:center}
.video{left:624px;top:646px;width:478px;height:287px;border:4px solid var(--white);outline:1px solid var(--line);background:linear-gradient(135deg,#8fa3b5,#d9dde2 45%,#6b7a88)}
.play{left:836px;top:762px}
.rule{left:98px;width:1004px;height:1px;background:var(--line)}

/* section titles */
.sec-title{left:0;width:1200px;text-align:center;font-size:26px;font-weight:300;color:#555;letter-spacing:.5px}
.sec-title b{color:var(--blue);font-weight:700}

/* flights */
.flight{top:1100px;width:236px;height:237px;border:1px solid var(--line);background:var(--white)}
.flight .ph{height:190px}
.flight .cap{text-align:center;font-size:17px;font-weight:600;color:var(--ink);padding-top:12px}

/* testimonial */
.testimonial{left:0;top:1395px;width:1200px;height:231px;background:var(--blue)}
.avatar{left:113px;top:1450px;width:122px;height:122px;border-radius:50%;border:4px solid var(--white);background:linear-gradient(#b9c4cf,#8c99a7)}
.t-rule{left:270px;top:1450px;width:1px;height:122px;background:rgba(255,255,255,.5)}
.t-quote{left:303px;top:1452px;width:790px;font-size:14px;font-style:italic;line-height:26px;color:var(--white)}
.t-name{left:307px;top:1546px;font-size:17px;font-weight:600;color:var(--white)}
.arrow{top:1495px}

/* news */
.news{top:1738px;width:320px}
.news .ph{height:213px;border:4px solid var(--white);outline:1px solid var(--line)}
.news h3{margin-top:26px;font-size:18px;font-weight:600;color:var(--ink)}
.news p{margin-top:10px;font-size:12.5px;line-height:21px;color:var(--text);padding-bottom:12px;border-bottom:1px solid var(--line)}
.news .meta{margin-top:14px;font-size:12px;color:var(--muted);display:flex;gap:22px}
.news .meta span{display:flex;align-items:center;gap:6px}
.date{top:1879px;width:47px;height:62px;background:var(--blue);color:var(--white);text-align:center;padding-top:6px}
.date b{display:block;font-size:22px;line-height:26px}
.date small{font-size:13px}

/* why book */
.devices{left:112px;top:2221px;width:407px;height:323px;background:linear-gradient(180deg,#dfe6ee,#b8c6d6 60%,#e8ebef)}
.why-title{left:581px;top:2224px;font-size:26px;font-weight:300;color:#555}
.why-title b{color:var(--blue);font-weight:700}
.why-sub{left:581px;top:2270px;font-size:14.5px;font-style:italic;font-weight:600;color:#444}
.feature{left:581px;display:flex;gap:16px}
.feature h4{font-size:16px;font-weight:400;color:var(--ink)}
.feature p{font-size:12px;color:var(--text);margin-top:5px}

/* footer */
.footer-top{left:0;top:2615px;width:1200px;height:4px;background:var(--blue)}
.partner{left:113px;font-weight:700;color:#24374f;white-space:nowrap}
.partner-a{top:2670px;font-size:38px}
.partner-b{top:2762px;font-size:28px;letter-spacing:2px}
.f-head{top:2654px;font-size:17px;font-weight:600;color:var(--ink)}
.f-links{left:378px;top:2690px;list-style:none;font-size:12.5px;color:var(--text);line-height:27px}
.f-text{font-size:12.5px;line-height:21px;color:var(--text)}
.nl-input{left:564px;top:2742px;width:252px;height:36px;border:1px solid var(--line);font-size:12px;color:#aaa;padding:10px 12px}
.btn-sub{left:564px;top:2793px;width:97px;height:33px;font-size:11px}
.contact-row{left:885px;display:flex;gap:14px;font-size:12.5px;line-height:21px;color:var(--text)}
.bottom-rule{left:98px;top:2862px;width:1004px;height:1px;background:var(--line)}
.copy{left:98px;top:2892px;font-size:12px;color:var(--text)}
.social{left:943px;top:2882px;display:flex;gap:14px}
.social span{width:34px;height:34px;border-radius:50%;border:1px solid #b7c6dc;display:flex;align-items:center;justify-content:center}
</style>
</head>
<body>

<!-- Header -->
<div class="abs brand"><span class="brand-dot"></span><span class="brand-name">SkyMerrow Airways</span></div>
<div class="abs phone-box">
  <span class="phone-icon"><svg width="14" height="14" viewBox="0 0 24 24"><path fill="#3b6cb7" d="M6.6 10.8a15.1 15.1 0 006.6 6.6l2.2-2.2c.3-.3.7-.4 1-.2 1.1.4 2.3.6 3.6.6.6 0 1 .4 1 1V20c0 .6-.4 1-1 1A17 17 0 013 4c0-.6.4-1 1-1h3.5c.6 0 1 .4 1 1 0 1.3.2 2.5.6 3.6.1.3 0 .7-.2 1z"/></svg></span>
  <div><div class="phone-label">Reservations &amp; Customer Service</div><div class="phone-number">1-800-555-0147</div></div>
</div>
<a class="abs btn btn-book-top">BOOK NOW!</a>

<nav class="abs nav">
  <span class="nav-item active" style="left:98px">HOME</span>
  <span class="nav-item" style="left:176px">FLIGHTS</span>
  <span class="nav-item" style="left:268px">CHARTER &amp; FLEET</span>
  <span class="nav-item" style="left:427px">PACKAGES</span>
  <span class="nav-item" style="left:538px">GALLERY</span>
  <span class="nav-item" style="left:634px">CONTACT</span>
  <span class="nav-item" style="left:737px">FAQ</span>
</nav>
<div class="abs search">Search<svg width="15" height="15" viewBox="0 0 24 24"><circle cx="10" cy="10" r="7" fill="none" stroke="#555" stroke-width="3"/><path d="M15 15l7 7" stroke="#555" stroke-width="3"/></svg></div>

<!-- Hero -->
<div class="abs hero" role="img" aria-label="Toronto skyline across the harbour at sunset with the city's landmark tower"></div>
<h1 class="abs hero-title">SKYMERROW AIRWAYS</h1>
<div class="abs booking"></div>
<div class="abs trip-types">
  <span><i class="radio on"></i>Round Trip</span><span><i class="radio"></i>One Way</span><span><i class="radio"></i>Open Jaw</span>
</div>
<div class="abs field" style="left:200px;width:178px">FROM</div>
<div class="abs field" style="left:378px;width:180px">TO</div>
<div class="abs field" style="left:558px;width:115px"><svg width="11" height="11" viewBox="0 0 12 12"><rect x="1" y="2" width="10" height="9" fill="none" stroke="#888"/><path d="M1 5h10" stroke="#888"/></svg>DEPART</div>
<div class="abs field" style="left:673px;width:112px"><svg width="11" height="11" viewBox="0 0 12 12"><rect x="1" y="2" width="10" height="9" fill="none" stroke="#888"/><path d="M1 5h10" stroke="#888"/></svg>RETURN</div>
<div class="abs field" style="left:785px;width:62px"><svg width="14" height="11" viewBox="0 0 14 12"><circle cx="5" cy="3" r="2.5" fill="#888"/><path d="M0 12c0-4 10-4 10 0z" fill="#888"/><circle cx="10" cy="4" r="2" fill="#888"/></svg>2</div>
<a class="abs btn btn-book-hero">BOOK NOW!</a>
<div class="abs dots"><i class="on"></i><i></i><i></i><i></i></div>

<!-- Welcome -->
<div class="abs welcome-pre">WELCOME TO</div>
<h2 class="abs welcome-title">SKYMERROW AIRWAYS</h2>
<div class="abs welcome-body">
  <p>At vero eos et accusamus et iusto odio dignissimos ducimus qui blanditiis praesentium voluptatum deleniti atque corrupti quos.</p>
  <p>Dolores et quas molestias excepturi sint occaecati cupiditate non provident similique sunt in culpa qui officia deserunt mollitia animi, id est laborum et dolorum fuga. Eha rum quidem rerum facilis est et expedita distinctio. Nam libero tempore, cum soluta nobis est eligendi omnis voluptas assumenda.</p>
</div>
<a class="abs btn-more">READ MORE &gt;&gt;</a>
<div class="abs video" role="img" aria-label="Video still of the SkyMerrow aircraft fuselage close up"></div>
<svg class="abs play" width="56" height="56" viewBox="0 0 56 56"><circle cx="28" cy="28" r="28" fill="#1e1e1e"/><path d="M22 17l18 11-18 11z" fill="#fff"/></svg>

<div class="abs rule" style="top:990px"></div>

<!-- Our Flights -->
<h2 class="abs sec-title" style="top:1034px">OUR <b>FLIGHTS</b></h2>
<div class="abs flight" style="left:98px"><div class="ph" role="img" aria-label="First class cabin with leather seats" style="background:linear-gradient(135deg,#6b5a48,#d8c6a8)"></div><div class="cap">FIRST CLASS</div></div>
<div class="abs flight" style="left:354px"><div class="ph" role="img" aria-label="Premium class private jet cabin" style="background:linear-gradient(135deg,#4a4a4a,#bfb6a6)"></div><div class="cap">PREMIUM CLASS</div></div>
<div class="abs flight" style="left:609px"><div class="ph" role="img" aria-label="Business class cabin with set dining table" style="background:linear-gradient(135deg,#a38f74,#eee3d2)"></div><div class="cap">BUSINESS CLASS</div></div>
<div class="abs flight" style="left:865px"><div class="ph" role="img" aria-label="Economy cabin with rows of seats" style="background:linear-gradient(135deg,#2f3236,#c9ccd0)"></div><div class="cap">ECONOMY</div></div>

<!-- Testimonial -->
<div class="abs testimonial"></div>
<svg class="abs arrow" style="left:34px" width="20" height="36" viewBox="0 0 20 36"><path d="M16 4L4 18l12 14" fill="none" stroke="#fff" stroke-width="3"/></svg>
<svg class="abs arrow" style="left:1146px" width="20" height="36" viewBox="0 0 20 36"><path d="M4 4l12 14L4 32" fill="none" stroke="#fff" stroke-width="3"/></svg>
<div class="abs avatar" role="img" aria-label="Portrait of customer Marcel Ouvrard"></div>
<div class="abs t-rule"></div>
<p class="abs t-quote">Nam libero tempore, cum soluta nobis est eligendi optio cumque nihil impedit quo minus id quod maxime placeat facere possimus, omnis voluptas assumenda est, omnis dolor repellendus. Temporibus autem quibusdam et aut officiis debitis aut rerum necessitatibus saepe eveniet ut et voluptates repudiandae sint et molestiae</p>
<div class="abs t-name">- Marcel Ouvrard</div>

<!-- Latest News -->
<h2 class="abs sec-title" style="top:1680px">LATEST <b>NEWS</b></h2>
<article class="abs news" style="left:98px">
  <div class="ph" role="img" aria-label="Aerial view of lake islands" style="background:linear-gradient(180deg,#9cb7d6,#4b7792 50%,#3f6a52)"></div>
  <h3>Finibus Bonorum et Malorum</h3>
  <p>Nam libero tempore, cum soluta nobis est eligendi optio cumque nihil impedit quo minus id quod maxim.</p>
  <div class="meta"><span><svg width="11" height="11" viewBox="0 0 12 12"><circle cx="6" cy="3.5" r="3" fill="#aaa"/><path d="M0 12c0-5 12-5 12 0z" fill="#aaa"/></svg>John Doe</span><span><svg width="13" height="11" viewBox="0 0 14 12"><path d="M1 1h12v7H6l-3 3V8H1z" fill="none" stroke="#aaa"/></svg>3 Comments</span></div>
</article>
<article class="abs news" style="left:442px">
  <div class="ph" role="img" aria-label="Twin-engine aircraft on the runway in front of the city skyline" style="background:linear-gradient(180deg,#8fb2d8,#c6d3de 50%,#6b6f6a)"></div>
  <h3>Finibus Bonorum et Malorum</h3>
  <p>Nam libero tempore, cum soluta nobis est eligendi optio cumque nihil impedit quo minus id quod maxim.</p>
  <div class="meta"><span><svg width="11" height="11" viewBox="0 0 12 12"><circle cx="6" cy="3.5" r="3" fill="#aaa"/><path d="M0 12c0-5 12-5 12 0z" fill="#aaa"/></svg>John Doe</span><span><svg width="13" height="11" viewBox="0 0 14 12"><path d="M1 1h12v7H6l-3 3V8H1z" fill="none" stroke="#aaa"/></svg>3 Comments</span></div>
</article>
<article class="abs news" style="left:785px">
  <div class="ph" role="img" aria-label="Terminal lounge with chairs overlooking the water" style="background:linear-gradient(135deg,#d9e4ee,#8fa8bf 50%,#3b3b3b)"></div>
  <h3>Finibus Bonorum et Malorum</h3>
  <p>Nam libero tempore, cum soluta nobis est eligendi optio cumque nihil impedit quo minus id quod maxim.</p>
  <div class="meta"><span><svg width="11" height="11" viewBox="0 0 12 12"><circle cx="6" cy="3.5" r="3" fill="#aaa"/><path d="M0 12c0-5 12-5 12 0z" fill="#aaa"/></svg>John Doe</span><span><svg width="13" height="11" viewBox="0 0 14 12"><path d="M1 1h12v7H6l-3 3V8H1z" fill="none" stroke="#aaa"/></svg>3 Comments</span></div>
</article>
<div class="abs date" style="left:90px"><b>01</b><small>NOV</small></div>
<div class="abs date" style="left:434px"><b>01</b><small>NOV</small></div>
<div class="abs date" style="left:777px"><b>01</b><small>NOV</small></div>

<div class="abs rule" style="top:2155px"></div>

<!-- Why Book -->
<div class="abs devices" role="img" aria-label="Desktop monitor and smartphone showing the SkyMerrow website"></div>
<h2 class="abs why-title">WHY BOOK <b>WITH US</b></h2>
<p class="abs why-sub">Comparable to airline prices, you'll be surprised how affordable it really is.</p>
<div class="abs feature" style="top:2332px">
  <svg width="24" height="24" viewBox="0 0 24 24"><path fill="#3b6cb7" d="M21 16v-2l-8-5V3.5a1.5 1.5 0 00-3 0V9l-8 5v2l8-2.5V19l-2 1.5V22l3.5-1 3.5 1v-1.5L13 19v-5.5z"/></svg>
  <div><h4>VIP Business Travel</h4><p>Say goodbye to check-in lines, baggage pick up, and customs. Arrive 15 minutes.</p></div>
</div>
<div class="abs feature" style="top:2408px">
  <svg width="24" height="24" viewBox="0 0 24 24"><rect x="3" y="4" width="18" height="17" fill="none" stroke="#3b6cb7" stroke-width="2"/><path d="M3 9h18M8 2v4M16 2v4M7 13h2M11 13h2M15 13h2M7 17h2M11 17h2" stroke="#3b6cb7" stroke-width="2"/></svg>
  <div><h4>Executive Class Terminal</h4><p>Enjoy complimentary WIFI and Harbor Roast coffee and teas in the private Lakeview FBO.</p></div>
</div>
<div class="abs feature" style="top:2486px">
  <svg width="24" height="24" viewBox="0 0 24 24"><circle cx="12" cy="12" r="10" fill="#3b6cb7"/><path d="M12 6v6l4 2" stroke="#fff" stroke-width="2" fill="none"/></svg>
  <div><h4>Saves you time</h4><p>Long drive to a destination without an international airport? Fly direct to a GA airports.</p></div>
</div>

<!-- Footer -->
<div class="abs footer-top"></div>
<div class="abs partner partner-a">tavlo</div>
<div class="abs partner partner-b">QUENBROOK</div>

<h4 class="abs f-head" style="left:378px">Quick Links</h4>
<ul class="abs f-links"><li>About Us</li><li>Contact Us</li><li>Terms and Conditions</li><li>Privacy Policy</li><li>FAQ</li></ul>

<h4 class="abs f-head" style="left:564px">Newsletter Subscription</h4>
<p class="abs f-text" style="left:564px;top:2690px;width:250px">Register your Email Address to get information about us</p>
<div class="abs nl-input">Email Address</div>
<a class="abs btn btn-sub">SUBSCRIBE</a>

<h4 class="abs f-head" style="left:885px">Contact Us</h4>
<div class="abs contact-row" style="top:2690px"><svg width="12" height="16" viewBox="0 0 12 16"><path d="M6 0a6 6 0 00-6 6c0 4.5 6 10 6 10s6-5.5 6-10a6 6 0 00-6-6zm0 8.5A2.5 2.5 0 116 3.5a2.5 2.5 0 010 5z" fill="#3b6cb7"/></svg><span>Corwin Hale Airfield<br>Hangar 4, Suite 210, Toronto, Ontario<br>M0X 0A0</span></div>
<div class="abs contact-row" style="top:2770px"><svg width="14" height="14" viewBox="0 0 24 24"><path fill="#3b6cb7" d="M6.6 10.8a15.1 15.1 0 006.6 6.6l2.2-2.2c.3-.3.7-.4 1-.2 1.1.4 2.3.6 3.6.6.6 0 1 .4 1 1V20c0 .6-.4 1-1 1A17 17 0 013 4c0-.6.4-1 1-1h3.5c.6 0 1 .4 1 1 0 1.3.2 2.5.6 3.6.1.3 0 .7-.2 1z"/></svg><span>1-800-555-0147</span></div>
<div class="abs contact-row" style="top:2808px"><svg width="14" height="12" viewBox="0 0 14 12"><rect x="0" y="1" width="14" height="10" fill="#3b6cb7"/><path d="M0 1l7 5 7-5" stroke="#fff" fill="none"/></svg><span style="text-decoration:underline">info@skymerrow-example.com</span></div>

<div class="abs bottom-rule"></div>
<p class="abs copy">© 2017, SkyMerrow Airways. All rights reserved.</p>
<div class="abs social">
  <span aria-label="Share"><svg width="14" height="14" viewBox="0 0 14 14"><circle cx="3" cy="7" r="2" fill="#3b6cb7"/><circle cx="11" cy="3" r="2" fill="#3b6cb7"/><circle cx="11" cy="11" r="2" fill="#3b6cb7"/><path d="M3 7l8-4M3 7l8 4" stroke="#3b6cb7" stroke-width="1.3"/></svg></span>
  <span aria-label="Email"><svg width="14" height="12" viewBox="0 0 14 12"><rect x=".5" y="1.5" width="13" height="9" fill="none" stroke="#3b6cb7"/><path d="M.5 1.5l6.5 5 6.5-5" fill="none" stroke="#3b6cb7"/></svg></span>
  <span aria-label="Website"><svg width="14" height="14" viewBox="0 0 14 14"><circle cx="7" cy="7" r="6" fill="none" stroke="#3b6cb7"/><ellipse cx="7" cy="7" rx="2.5" ry="6" fill="none" stroke="#3b6cb7"/><path d="M1 7h12" stroke="#3b6cb7"/></svg></span>
  <span aria-label="Message"><svg width="14" height="13" viewBox="0 0 14 13"><path d="M1 1h12v8H6l-3 3V9H1z" fill="none" stroke="#3b6cb7"/></svg></span>
</div>

</body>
</html>
```